Venture Capital Investment Firm

We are looking to overhaul our existing website (substantially), with only using the same logos (which we can provide).
We are an investment firm that focuses on making loans to late stage technology companies. Our site should ultimately look like other venture capital firms, and look modern and fresh. We have an existing website www.norvellhub.com which this will be replacing, although we will be using a lot of the existing written content, and potentially the numbers of pages we will need, we are not wed to anything else. Please feel free to shoot any questions at any time and thank you in advance for your help!
Websites we like as examples:
https://www.tesmarkfund.com/
https://www.brindlewoodpartners.com/
Target Market(s)
Potential investors who will invest in our firm, as well as potentially companies that are looking to borrow money from us.
Coding
Coded - Design and coding required
Number of Pages Required
5+ page
Colors
Designer to choose colors to be used in the design.
Look and feel

```html
<!DOCTYPE html>
<html lang="en">
<head>
<meta charset="utf-8">
<title>Norvell Hub – Flexible Capital</title>
<link rel="stylesheet" href="https://fonts.googleapis.com/css2?family=Rajdhani:wght@600;700&family=Montserrat:wght@400;500;600&display=swap">
<style>
:root{
  --navy:#21456b;
  --teal:#2a6469;
  --teal-deep:#215c62;
  --orange:#f26a2e;
  --ink:#1d1d1f;
  --muted:#6d6d72;
  --card:#efefef;
  --line:#d9d9d9;
  --white:#ffffff;
  --head:'Rajdhani',sans-serif;
  --body:'Montserrat',sans-serif;
}
*{box-sizing:border-box;margin:0;padding:0}
html,body{width:1200px;height:4219px;overflow:hidden}
body{position:relative;background:var(--white);font-family:var(--body);color:var(--ink)}
.abs{position:absolute}
.h-sec{font-family:var(--head);font-weight:700;font-size:36px;color:var(--ink);text-align:center;width:1200px;left:0}
.h-sec span,.accent{color:var(--orange)}
.h-sub{font-family:var(--head);font-weight:700;font-size:25px;color:var(--ink)}
.txt{font-size:11px;line-height:19.5px;color:var(--muted)}
.btn{display:flex;align-items:center;justify-content:center;border-radius:30px;background:var(--navy);color:var(--white);font-family:var(--head);font-weight:700;text-decoration:none}
.photo{background:linear-gradient(135deg,#8a8074,#3e4a50)}

/* header */
.site-header{top:0;left:0;width:1200px;height:90px;box-shadow:0 1px 6px rgba(0,0,0,.06)}
.brand{left:160px;top:22px;display:flex;align-items:center;gap:10px}
.brand-mark{width:36px;height:36px;border-radius:50%;background:var(--navy)}
.brand-name{font-family:var(--head);font-weight:700;font-size:32px;color:var(--navy);letter-spacing:.5px}
.nav{left:462px;top:37px;width:430px;display:flex;justify-content:space-between;font-size:11px;font-weight:500;white-space:nowrap}
.nav a{color:var(--ink);text-decoration:none}
.login{left:918px;top:28px;width:120px;height:35px;background:var(--orange);font-family:var(--body);font-weight:500;font-size:14px}

/* hero */
.hero-title{left:162px;top:218px;font-family:var(--head);font-weight:700;font-size:47px;line-height:56px;color:var(--ink)}
.hero-lead{left:162px;top:402px;width:470px;font-size:13px;line-height:22px;color:var(--muted)}
.investor-btn{left:161px;top:494px;width:195px;height:53px;font-size:17px}
.hero-art{left:0;top:0}
.slide-arrows{left:944px;top:669px;display:flex;gap:16px}
.slide-arrows span{width:29px;height:29px;border-radius:50%;background:var(--teal);display:flex;align-items:center;justify-content:center}

/* about */
.about-photo{left:147px;top:761px;width:410px;height:410px;border-radius:50%;border:10px solid #fff;box-shadow:0 2px 12px rgba(0,0,0,.15);overflow:hidden}
.about-title{left:613px;top:832px;font-family:var(--head);font-weight:700;font-size:36px}
.about-copy{left:613px;top:892px;width:430px}
.about-copy p+p{margin-top:19px}
.about-btn{left:611px;top:1076px;width:120px;height:44px;font-size:14px}

/* strategy */
.strategy-title{top:1248px}
.ls-title{top:1312px;left:0;width:1200px;text-align:center}
.ls-lead{top:1356px;left:370px;width:460px;text-align:center}
.focus-card{top:1432px;width:224px;height:238px;background:var(--card);border-radius:8px;text-align:center;padding-top:28px}
.focus-card h4{margin-top:14px;font-family:var(--head);font-weight:700;font-size:15px}
.focus-card p{margin:8px auto 0;width:196px;font-size:10px;line-height:19.5px;color:var(--muted)}

.tech-title{left:162px;top:1778px}
.tech-lead{left:162px;top:1812px;width:480px}
.tech-item{left:162px;display:flex;gap:28px}
.tech-item h5{font-family:var(--head);font-weight:700;font-size:14px;margin-bottom:4px}
.tech-item p{font-size:11px;line-height:19.5px;color:var(--muted);width:230px}
.tech-photo{left:617px;top:1781px;width:410px;height:410px;border-radius:50%;border:10px solid #fff;box-shadow:0 2px 12px rgba(0,0,0,.15);overflow:hidden}

.tt-title{top:2262px;left:0;width:1200px;text-align:center}
.tt-lead{top:2302px;left:390px;width:420px;text-align:center}
.step{width:210px;text-align:center}
.step-blob{width:110px;height:110px;margin:0 auto;border-radius:48% 52% 45% 55%/55% 45% 55% 45%;background:#fff;box-shadow:0 3px 12px rgba(0,0,0,.12);display:flex;align-items:center;justify-content:center}
.step h5{margin-top:18px;font-family:var(--head);font-weight:700;font-size:15px}
.step p{margin:6px auto 0;width:200px;font-size:10px;line-height:19.5px;color:var(--muted)}

/* team */
.team-title{top:2810px}
.member-name{left:162px;top:2950px;font-family:var(--head);font-weight:700;font-size:25px}
.member-role{left:162px;top:2990px;font-size:9px}
.member-role .tag{color:var(--orange)}
.member-role .area{color:var(--navy)}
.member-bio{left:162px;top:3014px;width:360px}
.member-bio p+p{margin-top:19px}
.team-btn{left:161px;top:3225px;width:120px;height:42px;font-size:14px}
.portrait{border-radius:50%;border:6px solid #fff;box-shadow:0 2px 10px rgba(0,0,0,.2);background:linear-gradient(160deg,#9a9a9a,#3a3a3a)}

/* news */
.news-title{top:3350px}
.news-card{top:3432px;width:280px;height:293px;background:#fff;box-shadow:0 1px 8px rgba(0,0,0,.12);border-bottom:3px solid var(--teal);padding:9px}
.news-img{position:relative;width:262px;height:164px}
.news-date{position:absolute;left:16px;top:16px;background:var(--teal);color:#fff;font-size:9px;padding:4px 12px}
.news-card h5{margin:12px 0 4px 4px;font-size:11.5px;font-weight:600}
.news-card p{margin-left:4px;font-size:10px;line-height:19.5px;color:var(--muted)}

/* footer */
.footer-bg{left:0;top:3755px}
.footer-brand{left:0;top:3888px;width:1200px;display:flex;justify-content:center;align-items:center;gap:14px}
.footer-brand .brand-mark{background:#fff;width:44px;height:44px}
.footer-brand .brand-name{color:#fff;font-size:38px;line-height:1}
.footer-brand small{display:block;font-family:var(--head);font-size:12px;letter-spacing:1px;color:#fff;margin-top:2px}
.contact{top:3999px;width:220px;text-align:center;color:#fff;font-size:11px;line-height:18px}
.contact .dot{width:46px;height:46px;border-radius:50%;background:#fff;margin:0 auto 12px;display:flex;align-items:center;justify-content:center}
.contact .label{color:var(--orange)}
.socials{left:486px;top:4114px;display:flex;gap:17px}
.socials span{width:32px;height:32px;border-radius:4px;background:var(--navy);box-shadow:0 1px 0 rgba(255,255,255,.15)}
.footer-rule{left:160px;top:4162px;width:880px;height:1px;background:rgba(255,255,255,.25)}
.copyright{left:0;top:4185px;width:1200px;text-align:center;font-size:11px;color:#fff}
</style>
</head>
<body>

<header class="site-header abs">
  <div class="brand abs"><span class="brand-mark"></span><span class="brand-name">Norvell Hub</span></div>
  <nav class="nav abs"><a href="#">Home</a><a href="#">About Us</a><a href="#">Strategy</a><a href="#">Investors</a><a href="#">Team</a><a href="#">News</a><a href="#">Contact Us</a></nav>
  <a class="btn login abs" href="#">Login Now</a>
</header>

<section class="hero">
  <svg class="hero-art abs" width="1200" height="760" viewBox="0 0 1200 760">
    <defs>
      <linearGradient id="heroPhoto" x1="0" y1="0" x2="1" y2="1">
        <stop offset="0" stop-color="#b9a58c"/><stop offset=".55" stop-color="#6f6356"/><stop offset="1" stop-color="#3c4a4e"/>
      </linearGradient>
      <linearGradient id="deskPhoto" x1="0" y1="0" x2="1" y2="1">
        <stop offset="0" stop-color="#d8d8d8"/><stop offset="1" stop-color="#2c2c2c"/>
      </linearGradient>
    </defs>
    <path d="M810 90 L1200 90 L1200 690 C1100 700 1010 650 935 595 C830 520 728 430 745 310 C758 215 790 150 810 90 Z" fill="var(--teal)"/>
    <g role="img" aria-label="Photo of a team joining hands in a circle above an office desk">
      <path d="M860 90 L1200 90 L1200 640 C1110 650 1020 610 955 560 C860 490 790 410 800 300 C808 215 840 150 860 90 Z" fill="url(#heroPhoto)"/>
    </g>
    <path d="M1050 640 C1110 620 1170 625 1200 640 L1200 690 C1140 695 1080 680 1050 640 Z" fill="var(--orange)"/>
    <circle cx="787" cy="650" r="92" fill="#fff" stroke="#e6e6e6" stroke-width="2"/>
    <circle cx="787" cy="650" r="82" fill="url(#deskPhoto)" role="img" aria-label="Photo of hands signing papers beside a laptop"/>
  </svg>
  <h1 class="hero-title abs">We Provide Flexible Capital<br>To Innovative Companies<br>And Their Investors</h1>
  <p class="hero-lead abs">We Are A Global Structured Credit Investment Firm Focused On The Healthcare And Technology Industries</p>
  <a class="btn investor-btn abs" href="#">Investor Login</a>
  <div class="slide-arrows abs">
    <span><svg width="14" height="14" viewBox="0 0 14 14"><path d="M12 7H3M7 3L3 7l4 4" stroke="#fff" stroke-width="2" fill="none"/></svg></span>
    <span><svg width="14" height="14" viewBox="0 0 14 14"><path d="M2 7h9M7 3l4 4-4 4" stroke="#fff" stroke-width="2" fill="none"/></svg></span>
  </div>
</section>

<section class="about">
  <div class="about-photo abs">
    <svg width="390" height="390" viewBox="0 0 390 390">
      <rect width="390" height="390" fill="#8c8a86" role="img" aria-label="Photo of a meeting room with a presenter at a whiteboard"/>
      <path d="M0 220 C60 260 100 340 170 390 L0 390 Z" fill="var(--teal)"/>
      <path d="M150 390 C220 320 320 300 390 320 L390 390 Z" fill="var(--orange)"/>
    </svg>
  </div>
  <h2 class="about-title abs">About <span class="accent">Us</span></h2>
  <div class="about-copy txt abs">
    <p>Norvell Hub is a private investment firm unique in its dual focus on life science and technology credit opportunities. Our ambidextrous approach to investing reflects a broad recognition and appreciation for the critical role intellectual property plays in the successful commercialization of products.</p>
    <p>We apply our extensive industry expertise to assess the revenue visibility created by these assets and offer a range of creative financing solutions.</p>
  </div>
  <a class="btn about-btn abs" href="#">Read More</a>
</section>

<section class="strategy">
  <h2 class="h-sec strategy-title abs">Our <span>Strategy</span></h2>
  <h3 class="h-sub ls-title abs">1. Life Sciences</h3>
  <p class="txt ls-lead abs" style="font-size:11.5px">Our focus spans the life science and technology industries, two sectors where intellectual property (IP) is an integral driver of asset and enterprise value.</p>

  <article class="focus-card abs" style="left:247px">
    <svg width="64" height="64" viewBox="0 0 64 64" fill="none" stroke="var(--teal)" stroke-width="2"><rect x="10" y="8" width="20" height="8"/><rect x="8" y="16" width="24" height="40" rx="3"/><circle cx="20" cy="40" r="7"/><circle cx="44" cy="42" r="12"/><path d="M38 48l12-12"/></svg>
    <h4>Biopharma</h4>
    <p>Lorem Ipsum is simply dummy text of the printing and typesetting industry. Lorem Ipsum has been the industry's standard dummy text.</p>
  </article>
  <article class="focus-card abs" style="left:488px">
    <svg width="64" height="64" viewBox="0 0 64 64" fill="none" stroke="var(--teal)" stroke-width="2"><rect x="20" y="6" width="26" height="52" rx="3"/><rect x="26" y="14" width="14" height="10"/><path d="M33 48V34M33 38c-6 0-8-4-8-4 6 0 8 4 8 4zM33 38c6 0 8-4 8-4-6 0-8 4-8 4z"/><path d="M8 40h8M12 36v8"/></svg>
    <h4>Devices</h4>
    <p>Lorem Ipsum is simply dummy text of the printing and typesetting industry. Lorem Ipsum has been the industry's standard dummy text.</p>
  </article>
  <article class="focus-card abs" style="left:727px">
    <svg width="64" height="64" viewBox="0 0 64 64" fill="none" stroke="var(--teal)" stroke-width="2"><path d="M22 16v16L10 54h26L26 32V16"/><path d="M20 16h8"/><rect x="40" y="28" width="8" height="26"/><path d="M52 38v16h6V38"/><path d="M8 58h50"/><circle cx="30" cy="8" r="1.5"/><circle cx="44" cy="12" r="1.5"/></svg>
    <h4>Tools &amp; Diagnostics</h4>
    <p>Lorem Ipsum is simply dummy text of the printing and typesetting industry. Lorem Ipsum has been the industry's standard dummy text.</p>
  </article>

  <h3 class="h-sub tech-title abs">2. Technology</h3>
  <p class="txt tech-lead abs">Our focus spans the life science and technology industries, two sectors where intellectual property (IP) is an integral driver of asset and enterprise value.</p>

  <div class="tech-item abs" style="top:1886px">
    <svg width="48" height="50" viewBox="0 0 48 50" fill="none" stroke="var(--navy)" stroke-width="2"><rect x="2" y="2" width="40" height="44" rx="2"/><circle cx="20" cy="22" r="10"/><path d="M28 30l10 10"/><path d="M6 42h20"/></svg>
    <div><h5>Software &amp; Services</h5><p>Lorem Ipsum is simply dummy text of the printing and typesetting industry.</p></div>
  </div>
  <div class="tech-item abs" style="top:1998px">
    <svg width="48" height="50" viewBox="0 0 48 50" fill="none" stroke="var(--navy)" stroke-width="2"><rect x="10" y="2" width="28" height="36" rx="2"/><path d="M16 10h16M16 16h16M16 22h16M16 28h10"/><path d="M2 38h44v8H2z"/></svg>
    <div><h5>Hardware</h5><p>Lorem Ipsum is simply dummy text of the printing and typesetting industry.</p></div>
  </div>
  <div class="tech-item abs" style="top:2110px">
    <svg width="48" height="50" viewBox="0 0 48 50" fill="none" stroke="var(--navy)" stroke-width="2"><rect x="2" y="2" width="44" height="44" rx="3"/><path d="M2 12h44"/><rect x="8" y="18" width="32" height="8"/><rect x="8" y="32" width="14" height="8"/><rect x="26" y="32" width="14" height="8"/></svg>
    <div><h5>Systems</h5><p>Lorem Ipsum is simply dummy text of the printing and typesetting industry.</p></div>
  </div>

  <div class="tech-photo abs">
    <svg width="390" height="390" viewBox="0 0 390 390">
      <rect width="390" height="390" fill="#5b5046" role="img" aria-label="Photo of a businessman checking his phone at a laptop"/>
      <path d="M0 190 C60 230 80 320 120 390 L0 390 Z" fill="var(--teal)"/>
      <path d="M90 390 C170 310 300 290 390 300 L390 390 Z" fill="var(--orange)"/>
    </svg>
  </div>

  <h3 class="h-sub tt-title abs">3. Transaction Type</h3>
  <p class="txt tt-lead abs">We uniquely offer sizeable and flexible structured credit financing solutions to innovative technology companies, with a focus on enterprise software.</p>

  <svg class="abs" style="left:380px;top:2440px" width="420" height="110" viewBox="0 0 420 110" fill="none" stroke="#8aa6a9" stroke-width="1.2" stroke-dasharray="2 3">
    <path d="M20 100 C70 60 130 50 170 52"/>
    <path d="M270 52 C330 50 380 30 410 2"/>
  </svg>

  <div class="step abs" style="left:255px;top:2510px">
    <div class="step-blob"><svg width="64" height="44" viewBox="0 0 64 44" fill="none" stroke="var(--teal)" stroke-width="2"><rect x="2" y="2" width="44" height="28" rx="3"/><path d="M2 10h44"/><rect x="16" y="14" width="46" height="28" rx="3"/><path d="M22 30h14"/></svg></div>
    <h5>Structured&nbsp; Credit</h5>
    <p>Lorem Ipsum is simply dummy text of the printing and typesetting industry. Lorem Ipsum has been the industry's standard dummy text.</p>
  </div>
  <div class="step abs" style="left:493px;top:2432px">
    <div class="step-blob"><svg width="50" height="50" viewBox="0 0 50 50" fill="none" stroke="var(--teal)" stroke-width="2"><circle cx="25" cy="8" r="5"/><rect x="14" y="16" width="22" height="20"/><path d="M4 22h10M36 22h10M4 30h10M36 30h10M19 36v10M31 36v10"/></svg></div>
    <h5>Structured&nbsp; Credit</h5>
    <p>Lorem Ipsum is simply dummy text of the printing and typesetting industry. Lorem Ipsum has been the industry's standard dummy text.</p>
  </div>
  <div class="step abs" style="left:729px;top:2355px">
    <div class="step-blob"><svg width="54" height="50" viewBox="0 0 54 50" fill="none" stroke="var(--teal)" stroke-width="2"><path d="M4 22C4 10 14 2 27 2s23 8 23 20z"/><path d="M27 2v20M15 22C15 10 20 4 27 2M39 22C39 10 34 4 27 2"/><circle cx="16" cy="36" r="9"/><circle cx="38" cy="36" r="9"/><path d="M16 31v10M38 31v10"/></svg></div>
    <h5>Structured&nbsp; Credit</h5>
    <p>Lorem Ipsum is simply dummy text of the printing and typesetting industry. Lorem Ipsum has been the industry's standard dummy text.</p>
  </div>
</section>

<section class="team">
  <h2 class="h-sec team-title abs">Our <span>Team</span></h2>
  <h3 class="member-name abs">Elias Marwood</h3>
  <p class="member-role abs"><span class="tag">Managing Partner</span> &nbsp;|&nbsp; <span class="area">Life Sciences, Technology</span></p>
  <div class="member-bio txt abs">
    <p>Elias Marwood is an industry leader with over $1.2B in structured credit investments since 2004. Elias focuses on origination, underwriting, and portfolio management across sectors at Norvell Hub.</p>
    <p>Mr. Marwood was the co-founder of Brightfield Health Partners, a life sciences focused structured credit fund, from 2010-2014. From 2004-2010, Mr. Marwood was Managing Director and Co-Head of the Healthcare Group for the Keystone Special Opportunities Fund at Halden Investment Group.</p>
  </div>
  <a class="btn team-btn abs" href="#">Read More</a>

  <svg class="abs" style="left:620px;top:2880px" width="420" height="430" viewBox="0 0 420 430">
    <path d="M60 80 C90 10 180 -10 260 20 C340 50 300 150 360 200 C420 250 400 330 330 380 C260 420 150 420 90 370 C30 320 0 260 20 200 C35 150 40 110 60 80 Z" fill="#f7d6cb"/>
    <path d="M110 60 C150 10 230 10 280 40 C340 80 310 170 380 230 C420 270 390 350 330 390 C270 430 170 420 120 370 C80 330 100 260 80 200 C60 140 80 100 110 60 Z" fill="var(--teal)" role="img" aria-label="Photo of colleagues working together in an office"/>
  </svg>
  <div class="portrait abs" style="left:831px;top:2874px;width:112px;height:112px" role="img" aria-label="Portrait of a partner"></div>
  <div class="portrait abs" style="left:578px;top:3026px;width:182px;height:182px" role="img" aria-label="Portrait of Elias Marwood"></div>
  <div class="portrait abs" style="left:888px;top:3204px;width:92px;height:92px" role="img" aria-label="Portrait of a partner"></div>
</section>

<section class="news">
  <h2 class="h-sec news-title abs">Latest <span>News</span></h2>
  <article class="news-card abs" style="left:160px">
    <div class="news-img photo" role="img" aria-label="Photo of a man working at a laptop by a window"><span class="news-date">16 November 2019</span></div>
    <h5>Lorem Ipsum is simply dummy text.</h5>
    <p>Lorem Ipsum is simply dummy text of the printing and typesetting industry. Lorem Ipsum has been the industry's standard dummy text ever since the 1500s.</p>
  </article>
  <article class="news-card abs" style="left:460px">
    <div class="news-img photo" style="background:linear-gradient(135deg,#d9dde0,#3b3f44)" role="img" aria-label="Photo of a calculator and pen over financial charts"><span class="news-date">16 November 2019</span></div>
    <h5>Lorem Ipsum is simply dummy text.</h5>
    <p>Lorem Ipsum is simply dummy text of the printing and typesetting industry. Lorem Ipsum has been the industry's standard dummy text ever since the 1500s.</p>
  </article>
  <article class="news-card abs" style="left:760px">
    <div class="news-img photo" style="background:linear-gradient(135deg,#b7b8ba,#e2e2e2)" role="img" aria-label="Photo of a smiling businesswoman"><span class="news-date">16 November 2019</span></div>
    <h5>Lorem Ipsum is simply dummy text.</h5>
    <p>Lorem Ipsum is simply dummy text of the printing and typesetting industry. Lorem Ipsum has been the industry's standard dummy text ever since the 1500s.</p>
  </article>
</section>

<footer>
  <svg class="footer-bg abs" width="1200" height="464" viewBox="0 0 1200 464">
    <path d="M0 40 C150 70 250 110 420 95 C600 80 700 110 880 70 C1000 45 1080 -20 1200 10 L1200 464 L0 464 Z" fill="var(--teal-deep)"/>
  </svg>
  <div class="footer-brand abs">
    <span class="brand-mark"></span>
    <div><span class="brand-name">Norvell Hub</span><small>INVESTMENT PARTNERS, LLC</small></div>
  </div>
  <svg class="abs" style="left:420px;top:4021px" width="360" height="2"><line x1="0" y1="1" x2="360" y2="1" stroke="rgba(255,255,255,.5)" stroke-dasharray="2 3"/></svg>
  <div class="contact abs" style="left:289px">
    <div class="dot"><svg width="16" height="20" viewBox="0 0 16 20"><path d="M8 1a6 6 0 0 0-6 6c0 5 6 12 6 12s6-7 6-12a6 6 0 0 0-6-6z" fill="var(--orange)"/><circle cx="8" cy="7" r="2.2" fill="#fff"/></svg></div>
    250 Larkin Row #310<br>Fairview, CA&nbsp; 94000
  </div>
  <div class="contact abs" style="left:483px">
    <div class="dot"><svg width="18" height="18" viewBox="0 0 18 18"><path d="M4 1l3 4-2 2c1 2 3 4 5 5l2-2 4 3-2 3C8 16 2 10 1 4z" fill="var(--orange)"/></svg></div>
    <span class="label">Call us on:</span><br>+1-555-000-0100
  </div>
  <div class="contact abs" style="left:678px">
    <div class="dot"><svg width="18" height="14" viewBox="0 0 18 14"><rect x="1" y="1" width="16" height="12" rx="1" fill="var(--orange)"/><path d="M1 2l8 6 8-6" stroke="#fff" stroke-width="1.4" fill="none"/></svg></div>
    <span class="label">Email:</span><br>inquiries@norvellhub.com
  </div>
  <div class="socials abs"><span></span><span></span><span></span><span></span><span></span></div>
  <div class="footer-rule abs"></div>
  <p class="copyright abs">Copyrights © 2019 Norvell Hub. All Rights Reserved. Terms &amp; Conditions | Privacy Policy.</p>
</footer>

</body>
</html>
```